A private security company called "Tavron Security Services Ltd"

Hello everybody,

We need a web page for a company based in NZ. It is mainly an informative website so it would be wonderful if the designer puts their absolute best into making it a website that I would really appreciate. The website needs to show professionalism and also needs to make our web surfers find the information they need in a click. the company's colour is black and silver, and if those two colours could be integrated into the website it would be absolutely lovely. Please do contact me for any information.

Sincerely,
Dorian Vaskel

Industry/Entity Type

Security

```html
<!DOCTYPE html>
<html lang="en">
<head>
<meta charset="utf-8">
<title>Tavron Security Services Ltd</title>
<link rel="stylesheet" href="https://fonts.googleapis.com/css2?family=Encode+Sans+Condensed:wght@400;500;600&family=Arimo:wght@400;700&display=swap">
<style>
:root{
  --ink:#111;
  --text:#444;
  --muted:#8a8a8a;
  --silver-1:#f4f4f4;
  --silver-2:#e3e3e3;
  --silver-3:#cfcfcf;
  --line:#c9c9c9;
  --dark-1:#4a4a4a;
  --dark-2:#2b2b2b;
  --dark-3:#1c1c1c;
  --footer-text:#b5b5b5;
  --white:#fff;
}
*{margin:0;padding:0;box-sizing:border-box}
html,body{width:1200px;height:2748px;overflow:hidden}
body{position:relative;font-family:"Arimo",Arial,sans-serif;color:var(--text);background:var(--white)}
section,header,footer{position:absolute;left:0;width:1200px}

/* header */
.site-header{top:0;height:157px;background:linear-gradient(#ffffff,#ececec);border-bottom:1px solid #ddd}
.brand{position:absolute;left:157px;top:52px;display:flex;align-items:center;gap:12px}
.brand-mark{width:30px;height:30px;border-radius:50%;background:var(--dark-2)}
.brand-name{font-family:"Encode Sans Condensed",sans-serif;font-weight:600;font-size:19px;line-height:22px;color:var(--ink);width:160px}
.tagline{position:absolute;left:418px;top:26px;font-family:"Arimo",sans-serif;font-size:24px;font-weight:700;font-variant:small-caps;letter-spacing:.5px;color:var(--ink);white-space:nowrap}
.main-nav{position:absolute;left:416px;top:100px;display:flex;white-space:nowrap}
.main-nav a{font-size:12.5px;color:#222;text-decoration:none;text-transform:uppercase;margin-right:26px;letter-spacing:.1px}
.main-nav a:last-child{margin-right:0}
.social{position:absolute;display:flex;gap:10px}
.social span{width:30px;height:30px;border-radius:50%;background:#b4b4b4;display:block}
.site-header .social{left:932px;top:32px}

/* hero */
.hero{top:157px;height:517px;background:radial-gradient(ellipse at 35% 40%,#5a5a5a 0%,#3a3a3a 45%,#222 100%)}
.hero-camera{position:absolute;left:697px;top:0;width:265px;height:517px;background:linear-gradient(90deg,rgba(255,255,255,0) 0%,rgba(210,210,215,.35) 40%,rgba(245,245,250,.55) 55%,rgba(160,160,165,.2) 80%,rgba(255,255,255,0) 100%)}
.hero-text{position:absolute;left:216px;top:228px;font-family:"Encode Sans Condensed",sans-serif;font-size:31px;line-height:48px;color:#f2f2f2;font-weight:400;white-space:nowrap}
.hero-text strong{font-weight:600;font-size:36px}
.slide-arrow{position:absolute;width:50px;height:50px;border-radius:50%;background:rgba(120,120,120,.75)}
.slide-arrow svg{position:absolute;left:15px;top:15px}
.hero .prev{left:103px;top:234px}
.hero .next{left:1045px;top:234px}

/* solutions */
.solutions{top:674px;height:711px;background:linear-gradient(#f3f3f3 0%,#ebebeb 60%,#dadada 100%)}
.section-title{position:absolute;left:0;width:1200px;text-align:center;font-family:"Encode Sans Condensed",sans-serif;font-weight:500;font-size:40px;color:var(--ink)}
.solutions .section-title{top:52px}
.services-side{position:absolute;left:157px;top:148px;width:212px}
.services-side h3{font-family:"Encode Sans Condensed",sans-serif;font-weight:500;font-size:23px;color:var(--ink);margin-bottom:14px}
.services-side ul{list-style:none}
.services-side li{position:relative;padding-left:33px;font-size:12.5px;line-height:16px;color:#777;margin-bottom:21px}
.services-side li::before{content:"";position:absolute;left:0;top:0;width:16px;height:16px;border-radius:50%;background:#ddd}
.services-side li::after{content:"";position:absolute;left:5px;top:5px;width:5px;height:5px;border-right:1.5px solid #888;border-top:1.5px solid #888;transform:rotate(45deg)}
.custom-box{position:absolute;left:157px;top:422px;width:212px;height:251px;background:linear-gradient(#efefef,#9c9c9c);text-align:center;padding-top:26px}
.custom-box p{font-family:"Encode Sans Condensed",sans-serif;font-size:25px;line-height:31px;color:#3a3a3a;font-weight:500}
.custom-box .box-name{font-family:"Encode Sans Condensed",sans-serif;font-size:17px;font-weight:600;color:#1f1f1f;margin-top:78px;line-height:20px;padding:0 20px}
.col-line{position:absolute;top:148px;width:1px;height:563px;background:var(--line)}
.card{position:absolute;width:222px;padding:0 14px}
.card .thumb{display:block;width:194px;height:102px;border:5px solid #fff;box-shadow:0 1px 3px rgba(0,0,0,.25)}
.card h4{font-family:"Encode Sans Condensed",sans-serif;font-weight:500;font-size:19px;color:var(--ink);margin:18px 0 6px;white-space:nowrap}
.card p{font-size:11.5px;line-height:14.5px;color:#888}
.btn-more{display:block;width:72px;height:25px;margin:8px 0 0 auto;background:linear-gradient(#fdfdfd,#dcdcdc);border:1px solid #bdbdbd;border-radius:3px;font-size:11px;line-height:23px;text-align:center;color:#222}
.row-line{position:absolute;height:1px;background:var(--line)}

/* industries */
.industries{top:1385px;height:402px;background:#fff}
.industries .section-title{top:43px}
.industry{position:absolute;top:147px;width:194px;text-align:center}
.industry .thumb{display:block;width:194px;height:156px;border:4px solid #e4e4e4}
.industry span{display:block;margin:12px -30px 0;font-family:"Encode Sans Condensed",sans-serif;font-weight:500;font-size:18px;color:var(--ink);white-space:nowrap}
.small-arrow{position:absolute;top:205px;width:34px;height:34px;border-radius:50%;background:#a9a9a9}
.small-arrow svg{position:absolute;left:10px;top:9px}

/* markets */
.markets{top:1787px;height:481px;background:linear-gradient(#ececec,#f6f6f6 40%,#f2f2f2)}
.markets .divider{position:absolute;left:600px;top:60px;width:2px;height:360px;background:linear-gradient(rgba(0,0,0,0),rgba(0,0,0,.12),rgba(0,0,0,0))}
.market{position:absolute;top:70px;width:390px;text-align:center}
.market .ring{width:176px;height:176px;border-radius:50%;background:#e0e0e0;margin:0 auto;padding:9px;box-shadow:0 2px 5px rgba(0,0,0,.15)}
.market .ring div{width:158px;height:158px;border-radius:50%}
.market h4{font-family:"Encode Sans Condensed",sans-serif;font-weight:500;font-size:18px;color:var(--ink);margin:28px 0 10px}
.market p{font-size:12.5px;line-height:15px;color:#999;padding:0 8px}
.market .btn-more{width:112px;height:31px;line-height:29px;font-size:12.5px;margin:22px auto 0}

/* footer */
.site-footer{top:2268px;height:480px;background:linear-gradient(#3c3c3c,#2a2a2a 60%,#242424)}
.site-footer h3{position:absolute;top:54px;font-family:"Encode Sans Condensed",sans-serif;font-weight:400;font-size:29px;color:#f2f2f2}
.about-text{position:absolute;left:157px;top:124px;width:302px;font-size:12px;line-height:15px;color:#8f8f8f}
.about-text p+p{margin-top:14px}
.quick-links{position:absolute;left:540px;top:125px;list-style:none;width:140px}
.quick-links li{position:relative;padding-left:22px;font-size:11.5px;line-height:15px;color:#a5a5a5;text-transform:uppercase;margin-bottom:17px}
.quick-links li::before{content:"";position:absolute;left:1px;top:4px;width:6px;height:6px;border-right:2px solid #eee;border-top:2px solid #eee;transform:rotate(45deg)}
.contact{position:absolute;left:766px;top:129px;width:300px}
.contact .co-name{font-size:12px;font-weight:700;letter-spacing:.6px;color:#9a9a9a;text-transform:uppercase;margin-bottom:22px}
.contact-row{display:flex;align-items:flex-start;gap:16px;font-size:12px;line-height:15px;color:#a5a5a5;margin-bottom:14px;text-transform:uppercase}
.contact-row.mail{text-transform:none}
.contact-row svg{flex:none;margin-top:1px}
.copy-bar{position:absolute;left:0;top:384px;width:1200px;height:96px;background:#262626;border-top:1px solid #333}
.copy-bar p{position:absolute;left:157px;top:44px;font-size:12px;color:#8a8a8a}
.copy-bar .social{left:932px;top:33px}
.copy-bar .social span{background:#8d8d8d}
</style>
</head>
<body>

<header class="site-header">
  <div class="brand">
    <span class="brand-mark"></span>
    <span class="brand-name">Tavron Security Services Ltd</span>
  </div>
  <div class="tagline">Steadfast by Design</div>
  <nav class="main-nav">
    <a href="#">Home</a>
    <a href="#">About Us</a>
    <a href="#">Our Security Solutions</a>
    <a href="#">Industries We Serve</a>
    <a href="#">Contact Us</a>
  </nav>
  <div class="social"><span></span><span></span><span></span></div>
</header>

<section class="hero">
  <div class="hero-camera" role="img" aria-label="Security camera mounted on a steel pole"></div>
  <div class="slide-arrow prev"><svg width="20" height="20" viewBox="0 0 20 20"><path d="M13 2 5 10l8 8" fill="none" stroke="#fff" stroke-width="2"/></svg></div>
  <div class="slide-arrow next"><svg width="20" height="20" viewBox="0 0 20 20"><path d="M7 2l8 8-8 8" fill="none" stroke="#fff" stroke-width="2"/></svg></div>
  <p class="hero-text"><strong>Lorem Ipsum</strong> is simply dummy text of<br>the printing and typesetting industry.</p>
</section>

<section class="solutions">
  <h2 class="section-title">Our Security Solutions</h2>

  <aside class="services-side">
    <h3>Services</h3>
    <ul>
      <li>Property guards</li>
      <li>Corporate events security</li>
      <li>Personal bodyguard for high net worth individuals</li>
      <li>Security consultancy</li>
      <li>Private investigation</li>
    </ul>
  </aside>
  <div class="custom-box">
    <p>CUSTOM OPTIONS<br>AVAILABLE</p>
    <div class="box-name">Tavron Security Services Ltd</div>
  </div>

  <div class="col-line" style="left:376px"></div>
  <div class="col-line" style="left:598px"></div>
  <div class="col-line" style="left:820px"></div>
  <div class="col-line" style="left:1042px"></div>
  <div class="row-line" style="left:377px;top:400px;width:221px"></div>
  <div class="row-line" style="left:599px;top:416px;width:221px"></div>
  <div class="row-line" style="left:821px;top:382px;width:221px"></div>

  <article class="card" style="left:377px;top:153px">
    <div class="thumb" role="img" aria-label="Suburban house model" style="background:linear-gradient(#d9d3c8,#8b6a52)"></div>
    <h4>Property Guards</h4>
    <p>Lorem ipsum dolor sit amet, cons ectetuer adipiscing elit, sed diam nonummy nibh.</p>
    <span class="btn-more">Read More</span>
  </article>
  <article class="card" style="left:377px;top:418px">
    <div class="thumb" role="img" aria-label="Event security staff in uniform" style="background:linear-gradient(#8a96a8,#1f2633)"></div>
    <h4>Corporate Events Security</h4>
    <p>Lorem ipsum dolor sit amet, cons ectetuer adipiscing elit, sed diam nonummy nibh euismod tincidunt ut laoreet dolore.</p>
    <span class="btn-more">Read More</span>
  </article>

  <article class="card" style="left:599px;top:153px">
    <div class="thumb" role="img" aria-label="Bodyguard in dark suit" style="background:linear-gradient(#3a4150,#111)"></div>
    <h4>Personal Bodyguards</h4>
    <p>Duis autem vel eum iriure dolor i n hendrerit in vulputate velit esse molestie consequat.</p>
    <span class="btn-more">Read More</span>
  </article>
  <article class="card" style="left:599px;top:434px">
    <div class="thumb" role="img" aria-label="Consultants in a business meeting" style="background:linear-gradient(#b7bcc2,#4d5157)"></div>
    <h4>Security Consultancy</h4>
    <p>Duis autem vel eum iriure dolor in hendrerit in vulputate velit ess e molestie consequat, vel illum d olore eu feugiat nulla.</p>
    <span class="btn-more">Read More</span>
  </article>

  <article class="card" style="left:821px;top:153px">
    <div class="thumb" role="img" aria-label="Investigator watching from a car" style="background:linear-gradient(#cfd6de,#5b6670)"></div>
    <h4>Private Investigation</h4>
    <p>Ut wisi enim ad minim veniam, qu is nostrud exerci tation ullamcorp er suscipit lobortis.</p>
    <span class="btn-more">Read More</span>
  </article>
  <article class="card" style="left:821px;top:396px">
    <div class="thumb" role="img" aria-label="Protection team beside a black car" style="background:linear-gradient(#8a8a8a,#1a1a1a)"></div>
    <h4>Executive Protection</h4>
    <p>Lorem ipsum dolor sit amet, cons ectetuer adipiscing elit, sed diam nonummy nibh euismod tincidunt ut laoreet dolore magna aliquam erat volutpat.</p>
    <span class="btn-more">Read More</span>
  </article>
</section>

<section class="industries">
  <h2 class="section-title">Industries We Serve</h2>
  <div class="small-arrow" style="left:109px"><svg width="14" height="16" viewBox="0 0 14 16"><path d="M10 2 4 8l6 6" fill="none" stroke="#fff" stroke-width="2"/></svg></div>
  <div class="small-arrow" style="left:1057px"><svg width="14" height="16" viewBox="0 0 14 16"><path d="M4 2l6 6-6 6" fill="none" stroke="#fff" stroke-width="2"/></svg></div>
  <div class="industry" style="left:157px">
    <div class="thumb" role="img" aria-label="Flag flying over a government building" style="background:linear-gradient(#3f6fb8,#9db4d4 60%,#7a7a7a)"></div>
    <span>Government</span>
  </div>
  <div class="industry" style="left:391px">
    <div class="thumb" role="img" aria-label="Solar panels and wind turbines" style="background:linear-gradient(#7fb0e6,#3d6fb0 55%,#1d3d78)"></div>
    <span>Energy and Environment</span>
  </div>
  <div class="industry" style="left:619px">
    <div class="thumb" role="img" aria-label="Oil pumps at sunset" style="background:linear-gradient(#e8a13a,#d2541c 55%,#1a0c06)"></div>
    <span>Oil and Gas</span>
  </div>
  <div class="industry" style="left:847px">
    <div class="thumb" role="img" aria-label="Cargo plane, truck and ship" style="background:linear-gradient(#f4f4f4,#c9c9c9)"></div>
    <span>Transportation and Logistics</span>
  </div>
</section>

<section class="markets">
  <div class="divider"></div>
  <div class="market" style="left:133px">
    <div class="ring"><div role="img" aria-label="Home owner at a front door keypad" style="background:linear-gradient(135deg,#c9b49a,#7a5a42)"></div></div>
    <h4>Residential Solutions</h4>
    <p>Lorem ipsum dolor sit amet, consectetur adipiscing elit. Sed in porta ut mauris vitae accumsan. Ut bibendum condim. Phasellus placerat lectus nec odio fermentum, non Proin nec ligula condimentum, aliquet nisi id,</p>
    <span class="btn-more">Read More</span>
  </div>
  <div class="market" style="left:672px">
    <div class="ring"><div role="img" aria-label="Guard standing before office towers" style="background:linear-gradient(135deg,#8fb3dc,#2b3f5c)"></div></div>
    <h4>Commercial Solutions</h4>
    <p>Lorem ipsum dolor sit amet, consectetur adipiscing elit. Sed in porta ut mauris vitae accumsan. Ut bibendum condim. Phasellus placerat lectus nec odio fermentum, non Proin nec ligula condimentum, aliquet nisi id,</p>
    <span class="btn-more">Read More</span>
  </div>
</section>

<footer class="site-footer">
  <h3 style="left:157px">About us</h3>
  <h3 style="left:540px">Quick Links</h3>
  <h3 style="left:766px">Contact Us</h3>
  <div class="about-text">
    <p>Lorem ipsum dolor sit amet, consectetur adipiscing elit. Morbi pellentesque iaculis justo eget fermentum. Pellentesque commodo iaculis neque, vitae tincidun odio pellentesque luctus. Aenean in eros eu magna vestibulum imperdiet pretium nec augue.</p>
    <p>Etiam quis turpis enim. Vestibulum auctor id mauris vulputate consequat. Suspendisse potenti. Cras at imperdiet elit. Integer fringilla tellus non diam condimentum, sed ultricies urna ultricies. Sed cong dui quis dui convallis dictum. Donec malesuada vulputate risus vitae vulputate. Maecenas in congue urna. Sed porttitor bibendum.</p>
  </div>
  <ul class="quick-links">
    <li>Home</li>
    <li>About Us</li>
    <li>Our Security Solutions</li>
    <li>Industries We Serve</li>
    <li>Contact Us</li>
  </ul>
  <div class="contact">
    <div class="co-name">Tavron Security Services Ltd.</div>
    <div class="contact-row">
      <svg width="14" height="18" viewBox="0 0 14 18"><path d="M7 0a7 7 0 0 0-7 7c0 5 7 11 7 11s7-6 7-11a7 7 0 0 0-7-7zm0 10a3 3 0 1 1 0-6 3 3 0 0 1 0 6z" fill="#eee"/></svg>
      <span>12 Harbour Rd, Westmere,<br>Auckland 1022, New Zealand</span>
    </div>
    <div class="contact-row">
      <svg width="15" height="15" viewBox="0 0 15 15"><path d="M3 0l3 3.5-1.8 2a9 9 0 0 0 5.3 5.3l2-1.8L15 12l-2 3C6 15 0 9 0 2z" fill="#eee"/></svg>
      <span>+64 9 555 0142</span>
    </div>
    <div class="contact-row mail">
      <svg width="16" height="12" viewBox="0 0 16 12"><rect width="16" height="12" fill="#eee"/><path d="M0 0l8 6 8-6" fill="none" stroke="#2b2b2b" stroke-width="1.5"/></svg>
      <span>info@tavronsecurity.co.nz</span>
    </div>
  </div>
  <div class="copy-bar">
    <p>Copyright © 2014 Tavron Security Service LTD.</p>
    <div class="social"><span></span><span></span><span></span></div>
  </div>
</footer>

</body>
</html>
```